Church Website with Home Page and Member Sermon Library

I am in need of an updated design for our church website. This will include 4 pages (outlined below). We are a conservative, evangelical, Christian church. The site should be modern and clean, while still reflecting our conservative values. I already have a logo for our church, and I want the site to incorporate the logo, and match the logo/branding. Stock photos are allowed if needed, but I have uploaded some images of our church and would prefer those images to be used if possible. Any stock photos used should not include any people in the photos (scenery, nature, buildings, animals, etc. are fine).

The site will need 4 pages: Home, Support Us (Donate), Login, and Recording Library.

Page 1: Home
The home page should include the following sections:

- Navigation: Should include links to each section of the home page plus a "listen live" link which will take the user to a live-streaming site and a "support us" link which will take the user to a support/donate page.

- Announcements: Can be either a banner or some other design, but there needs to be some way for us to post announcements for visitors to see. I'm open for creative ideas in this section, but would like it not to take up a lot of room on the page.

- About Us: Should include address, service times (see attached document), and information about the church.

- Pastor Bio: A section that introduces our pastor and gives a short bio about our pastor. Would like this section to include a picture of our pastor. Somewhere in this section I would like to include this Bible reference: "And I will give you pastors according to mine heart, which shall feed you with knowledge and understanding. Jer 3:15 LPW"

- Articles of Faith (What We Believe): This should include several sub-sections each with a heading, body, and possibly 1 or more scripture references. I have attached a document to the brief that includes our articles of faith. Feel free to be creative with this section in how you lay these out and format them.

- Support Us: A small section that explains what kind of support someone can give and a link to a donation page. The link can say something like "Support Us" or "Donate Now".

- Contact form: A contact form that allows the visitor to send us a message. The contact form should ask for name, email, phone, and message.

- Footer: A footer that will be displayed on all pages of the site. This should include at a minimum a link to the home page (or a link to each individual section in the home page if you prefer), a link to "listen live", a link to "support us", a link to "contact us" (or you can put the contact form directly in the footer if you prefer), the address, and a "member login" link.

Page 2: Support Us
The donation page should include a form the visitor can fill out to make a donation. We will embed a third party form later. For this design, please just mock out the design with a basic form asking for name, phone, and email.

Page 3: Login
The recording library (detailed below) will require members to login with a shared numeric code before accessing the page. We need a design for a login screen. The screen should include navigation/footer just like all other pages, but the body of the login page will consist only of a form that asks the user to enter the access code and then a "login" button.

Page 4: Recording Library

The library page is a member-only page that will require a shared, numeric pass code to access. On this page, members will be able to access a filterable list of past sermons. The page by default should display most recent sermons, but should also include a search form that allows the member to filter the sermon list to find a particular sermon. The search form should allow the user to select a filter type (e.g. Speaker name, date, event, etc.) and type in a value to search. They should be able to add multiple filters and remove filters that have been added. Each sermon that is displayed in the result list should include basic information such as title, date, speaker, tags, etc. along with a download icon, and an embedded audio player where they can click a play button to stream it on-demand. Each sermon should also have clickable tags associated with it that can be used to find related sermons.
Updates

I have uploaded several images of our church. Feel free to incorporate these into your design if possible.

Target Market(s)

Church Members

Industry/Entity Type

Religion

Number of Pages Required

4 page

Font styles to use
Sans Serif

Colors

Designer to choose colors to be used in the design.

Requirements
Must have
• Must incorporate the logo (attached)
Nice to have
• Would like the design to incorporate pictures of our church (attached) instead of stock photos if possible.
Should not have
• Please avoid an overly cluttered design. Stock photos used should not include any people in the photos.

```html
<!DOCTYPE html>
<html lang="en">
<head>
<meta charset="utf-8">
<title>Grace Covenant Church</title>
<link href="https://fonts.googleapis.com/css2?family=Playfair+Display:wght@400;700&family=Raleway:wght@400;500;600&family=Lato:wght@400;700&family=Oswald:wght@600&display=swap" rel="stylesheet">
<style>
:root{
  --green:#87a96b;
  --green-bright:#8cc152;
  --teal:#17b2d0;
  --dark:#151515;
  --dark-2:#2a2a2a;
  --faith:#0d3a3d;
  --text:#333;
  --muted:#666;
  --white:#fff;
}
*{box-sizing:border-box;margin:0;padding:0}
html,body{width:1200px;height:4796px;overflow:hidden}
body{position:relative;font-family:'Lato',sans-serif;color:var(--text);background:var(--white)}
.abs{position:absolute}
.btn{position:absolute;display:flex;align-items:center;justify-content:center;background:var(--teal);color:#fff;font-family:'Playfair Display',serif;font-weight:700;font-size:13px;letter-spacing:.5px;border-radius:22px;height:42px;text-transform:uppercase}
/* header */
.topbar{position:absolute;left:632px;top:0;width:568px;height:42px;background:var(--green);clip-path:polygon(38px 0,100% 0,100% 100%,0 100%);color:#fff;font-size:14px;display:flex;align-items:center;gap:26px;padding-left:80px}
.logo{position:absolute;display:flex;flex-direction:column;align-items:center;color:var(--green);font-family:'Raleway',sans-serif;font-weight:500}
.logo .mark{width:26px;height:26px;background:var(--green);margin-bottom:8px}
.nav{position:absolute;top:66px;left:632px;display:flex;align-items:center;font-family:'Playfair Display',serif;font-size:14px;color:#111}
.nav a{margin-right:46px;text-decoration:none;color:#111}
.nav a.active{color:var(--teal)}
.announce{position:absolute;top:134px;left:0;width:1200px;height:38px;background:var(--teal);color:#fff;display:flex;align-items:center;padding-left:106px;font-size:12px}
.announce b{font-family:'Playfair Display',serif;font-weight:400;font-size:16px;margin-right:14px}
/* hero */
.hero{position:absolute;top:172px;left:0;width:1200px;height:566px;background:radial-gradient(ellipse at 50% 40%,#6a4a35 0%,#3a2518 55%,#1d120b 100%)}
.hero-text{position:absolute;top:342px;width:1200px;text-align:center;color:#fff}
.hero-text .pre{font-family:'Playfair Display',serif;font-size:30px}
.hero-text h1{font-family:'Playfair Display',serif;font-weight:700;font-size:66px;line-height:1.15}
.hero-text h1 span{color:var(--green)}
.hero-text p{font-size:15px;margin-top:6px}
/* welcome */
.label{font-family:'Playfair Display',serif;font-size:18px;color:#333;letter-spacing:.5px;text-transform:uppercase}
.h2{font-family:'Playfair Display',serif;font-weight:700;font-size:44px;line-height:1.2;color:#111}
.para{font-size:15px;line-height:24px;color:#333}
.photo{position:absolute}
.brand-block{position:absolute;left:632px;top:1185px;width:456px;height:206px;background:var(--green);color:#fff;font-family:'Oswald',sans-serif;font-weight:600;font-size:80px;line-height:96px;letter-spacing:3px;padding:6px 0 0 14px;white-space:nowrap;overflow:hidden}
/* pastor */
.pastor{position:absolute;top:1443px;left:0;width:1200px;height:547px;background:var(--dark)}
.placeholder{position:absolute;left:106px;top:52px;width:476px;height:443px;background:var(--dark-2);display:flex;align-items:center;justify-content:center;color:#777;font-family:'Raleway',sans-serif;font-size:30px}
/* services */
.card{position:absolute;width:316px}
.card .img{width:316px;height:252px;position:relative}
.card .clock{position:absolute;right:0;bottom:-12px;width:40px;height:40px;background:#fff;display:flex;align-items:flex-start;justify-content:center;padding-top:6px}
.card h3{font-family:'Playfair Display',serif;font-weight:700;font-size:19px;margin:26px 0 14px;color:#222}
.card p{font-size:13px;line-height:22px;color:#444}
.divider{position:absolute;width:1px;background:#ddd}
/* faith */
.faith{position:absolute;top:2790px;left:0;width:1200px;height:586px;background:linear-gradient(90deg,#0b3134,#0f4548);clip-path:polygon(0 0,1004px 0,1200px 196px,1200px 100%,0 100%)}
.faith h2{position:absolute;left:106px;top:30px;font-family:'Playfair Display',serif;font-weight:700;font-size:40px;color:#fff}
.faith h3{font-family:'Raleway',sans-serif;font-weight:500;font-size:28px;color:var(--green-bright);margin-bottom:12px}
.faith p{font-size:14px;line-height:22px;color:#e8eeee}
.faith .item{position:absolute;left:108px;width:970px}
/* sermons */
.sermon{position:absolute;width:316px}
.sermon .frame{border:1px solid #e2e2e2;padding:10px;height:178px;background:#fff}
.sermon .frame div{width:100%;height:100%}
.sermon h4{font-family:'Raleway',sans-serif;font-weight:500;font-size:20px;margin-top:18px;color:#222}
.sermon .meta{font-size:11px;color:#777;margin-top:2px}
.sermon .icons{display:flex;gap:14px;margin-top:14px}
.sermon .icons svg{width:18px;height:16px}
.sermon p{font-size:12px;line-height:18px;color:#555;margin-top:14px}
/* footer */
.footer{position:absolute;top:4325px;left:0;width:1200px;height:471px;background:var(--dark);clip-path:polygon(186px 0,100% 0,100% 100%,0 100%,0 186px);color:#fff}
.footer h5{font-family:'Playfair Display',serif;font-weight:400;font-size:22px;color:var(--green);position:absolute;top:62px}
.flinks{position:absolute;top:116px;left:360px;font-size:13px;line-height:33px}
.contact-row{position:absolute;left:551px;display:flex;gap:14px;font-size:13px;line-height:20px}
.cicon{width:26px;height:26px;border:1px solid #444;display:flex;align-items:center;justify-content:center;flex:none}
.social{position:absolute;top:4566px;left:106px;display:flex;gap:14px}
.social span{width:38px;height:38px;border:2px solid #fff;border-radius:50%;display:block}
</style>
</head>
<body>

<!-- header -->
<div class="topbar">
  <span>&#9743; +2 (555) 240 6100</span>
  <span>&#9993; info@gracecovenantchurch.com</span>
</div>
<div class="logo" style="left:106px;top:10px;width:140px">
  <span class="mark"></span>
  <span style="font-size:20px;letter-spacing:1px">GRACE</span>
  <span style="font-size:10px;letter-spacing:5px">COVENANT</span>
</div>
<nav class="nav">
  <a class="active" href="#">HOME</a>
  <a href="#">LIBRARY</a>
  <a href="#">DONATION</a>
  <span class="btn" style="position:relative;width:144px;height:42px;font-size:12px">Donate Now</span>
</nav>
<div class="announce"><b>Excepteur sint occaecat:</b> Sed ut perspiciatis unde omnis iste natus error sit voluptatem accusantium doloremque enim ipsam voluptatem quia voluptas</div>

<!-- hero -->
<section class="hero" role="img" aria-label="Church interior with altar and candles"></section>
<svg class="abs" style="left:0;top:172px" width="1200" height="620" viewBox="0 0 1200 620">
  <polygon points="0,270 0,290 240,530 270,535" fill="var(--green)"/>
  <polygon points="0,300 0,385 255,620 275,620" fill="#fff"/>
  <polygon points="0,330 0,345 200,515 215,515" fill="var(--green)"/>
</svg>
<div class="hero-text">
  <div class="pre">God Will be</div>
  <h1>Raised to Life In <span>Christ</span></h1>
  <p>Sed ut perspiciatis unde omnis iste natus error sit dol voluptatem accusantium doloremque</p>
</div>
<span class="btn" style="left:522px;top:517px;width:156px">Explore More</span>

<!-- welcome -->
<section>
  <div class="abs" style="left:106px;top:912px;width:460px">
    <div class="label">Welcome to</div>
    <div class="h2" style="margin-top:10px">Grace Covenant<br>Church</div>
    <p class="para" style="margin-top:26px">Sed ut perspiciatis unde omnis iste natus error sit voluptatem accusantium doloremque laudantium, totam rem aperiam, eaque ipsa quae ab illo inventore veritatis et quasi architecto beatae vitae dicta sunt explicabo. Nemo enim ipsam voluptatem quia voluptas sit aspernatur aut odit aut fugit, sed quia...</p>
  </div>
  <span class="btn" style="left:106px;top:1252px;width:144px">Read More</span>
  <div class="photo" role="img" aria-label="Photograph of the church building" style="left:760px;top:818px;width:332px;height:520px;background:linear-gradient(180deg,#eeeeec 0%,#d2cec6 50%,#a8a196 100%)"></div>
  <svg class="abs" style="left:520px;top:900px" width="680" height="545" viewBox="0 0 680 545">
    <polygon points="10,0 35,0 680,530 680,545" fill="var(--green)"/>
    <polygon points="440,285 680,540 440,540" fill="var(--green)"/>
  </svg>
  <div class="brand-block">GRACE<br>COVENANT</div>
</section>

<!-- pastor -->
<section class="pastor">
  <svg class="abs" style="left:0;top:0" width="1200" height="547">
    <line x1="0" y1="165" x2="150" y2="15" stroke="#444" stroke-width="1"/>
    <line x1="40" y1="547" x2="110" y2="485" stroke="#444" stroke-width="1"/>
    <line x1="582" y1="60" x2="640" y2="5" stroke="#444" stroke-width="1"/>
    <line x1="560" y1="547" x2="620" y2="490" stroke="#444" stroke-width="1"/>
  </svg>
  <div class="placeholder" role="img" aria-label="Portrait of the pastor">580 X 540</div>
  <div class="abs" style="left:636px;top:100px;width:450px;color:#fff">
    <div class="label" style="color:#ddd">Pastor Bio</div>
    <div class="h2" style="color:#fff;font-size:42px;margin-top:8px">Jonathan Mercer</div>
    <p class="para" style="color:#ddd;margin-top:18px">Sed ut perspiciatis unde omnis iste natus error sit voluptatem accusantium doloremque laudantium, totam rem aperiam, eaque ipsa quae ab illo inventore veritatis et quasi architecto beatae vitae dicta sunt explicabo. Nemo enim ipsam voluptatem quia voluptas sit aspernatur aut odit aut fugit, sed quia consequuntur magni dolores eos qui ratione voluptatem sequi nesciunt.</p>
  </div>
  <span class="btn" style="left:636px;top:402px;width:144px">About Pastro</span>
</section>

<!-- services -->
<section>
  <div class="h2 abs" style="top:2060px;width:1200px;text-align:center">Our Church Services</div>
  <div class="divider" style="left:422px;top:2160px;height:540px"></div>
  <div class="divider" style="left:757px;top:2200px;height:540px"></div>
  <div class="card" style="left:106px;top:2180px">
    <div class="img" role="img" aria-label="Wooden church pew with a book" style="background:linear-gradient(135deg,#3a2a1c,#a87a4a 60%,#2a1d12)"><span class="clock"><svg width="24" height="24"><circle cx="12" cy="12" r="10" fill="none" stroke="var(--teal)" stroke-width="1.5"/><path d="M12 6v6l4 2" stroke="var(--teal)" stroke-width="1.5" fill="none"/></svg></span></div>
    <h3>Fringilla Justo Vestibulum</h3>
    <p>Sed ut perspiciatis unde omnis iste natus error sit voluptatem accusantium doloremque laudantm, totam rem aperiam...</p>
    <span class="btn" style="position:relative;display:flex;width:144px;margin-top:20px">Read More</span>
  </div>
  <div class="card" style="left:441px;top:2221px">
    <div class="img" role="img" aria-label="Sunrise over hills with a raised book" style="background:radial-gradient(circle at 25% 35%,#f2d8a0 0%,#a07a50 25%,#3a3038 70%,#1c1c22 100%)"><span class="clock"><svg width="24" height="24"><circle cx="12" cy="12" r="10" fill="none" stroke="var(--teal)" stroke-width="1.5"/><path d="M12 6v6l4 2" stroke="var(--teal)" stroke-width="1.5" fill="none"/></svg></span></div>
    <h3>Sollicitudin Tortor Tellus</h3>
    <p>Sed ut perspiciatis unde omnis iste natus error sit voluptatem accusantium doloremque laudantm, totam rem aperiam...</p>
    <span class="btn" style="position:relative;display:flex;width:144px;margin-top:20px">Read More</span>
  </div>
  <div class="card" style="left:776px;top:2262px">
    <div class="img" role="img" aria-label="Wooden cross beside an open book" style="background:radial-gradient(circle at 45% 40%,#c08a4a 0%,#5a3a20 40%,#1a120c 100%)"><span class="clock"><svg width="24" height="24"><circle cx="12" cy="12" r="10" fill="none" stroke="var(--teal)" stroke-width="1.5"/><path d="M12 6v6l4 2" stroke="var(--teal)" stroke-width="1.5" fill="none"/></svg></span></div>
    <h3>Ridiculus Condimentum</h3>
    <p>Sed ut perspiciatis unde omnis iste natus error sit voluptatem accusantium doloremque laudantm, totam rem aperiam...</p>
    <span class="btn" style="position:relative;display:flex;width:144px;margin-top:20px">Read More</span>
  </div>
</section>

<!-- faith -->
<section class="faith">
  <h2>Statement of Faith</h2>
  <div class="item" style="top:108px">
    <h3>The God Head</h3>
    <p>We believe in the God head bodily, known as the Divine Trinity. This body consist of God the father, Jesus Christ, his only begotten son and the redeemer of the world, and of the Holy Ghost, The third person of the Divine Trinity.</p>
  </div>
  <div class="item" style="top:230px">
    <h3>Sanctification</h3>
    <p>"Sanctify them through thy truth thy word is truth St John 17:17. For this is the will of God even your sanctification" We believe in a set apart life, separate from the world to Christ 2 Cor 6:17-18</p>
  </div>
  <div class="item" style="top:352px">
    <h3>Baptism of the Holy Ghost</h3>
    <p>We believe in the baptism of the Holy Ghost as it is taught in the Bible and promised by our Lord Jesus Christ, with speaking in tongues as the Spirit gives utterance as the initial evidence. Acts 2:4 we believe that the gift of the Holy Ghost is for all believers as the Lord promised. Acts 2:17-18</p>
  </div>
  <span class="btn" style="left:106px;top:502px;width:178px">View All Article</span>
</section>

<!-- sermons -->
<section>
  <div class="h2 abs" style="top:3444px;width:1200px;text-align:center">Latest Sermons</div>
  <svg width="0" height="0" style="position:absolute">
    <defs>
      <g id="i-video"><rect x="0" y="3" width="11" height="10" rx="1" fill="var(--green)"/><polygon points="11,8 18,3 18,13" fill="var(--green)"/></g>
      <g id="i-audio"><path d="M3 11a6 6 0 0 1 12 0" fill="none" stroke="var(--green)" stroke-width="2"/><rect x="1" y="10" width="4" height="6" rx="1" fill="var(--green)"/><rect x="13" y="10" width="4" height="6" rx="1" fill="var(--green)"/></g>
      <g id="i-cloud"><circle cx="6" cy="9" r="5" fill="var(--green)"/><circle cx="11" cy="7" r="6" fill="var(--green)"/><rect x="3" y="9" width="14" height="6" rx="3" fill="var(--green)"/></g>
      <g id="i-book"><path d="M3 1h12v15H3a2 2 0 0 1-2-2V3a2 2 0 0 1 2-2z" fill="var(--green)"/></g>
    </defs>
  </svg>
  <div class="sermon" style="left:106px;top:3525px"><div class="frame"><div role="img" aria-label="Hands raised in worship" style="background:linear-gradient(135deg,#2a2a2a,#8a7a6a 55%,#3a342e)"></div></div>
    <h4>Rebuilding The Walls</h4><div class="meta">Posted on 02 Apr 2013, Pastor: Daniel Hart</div>
    <div class="icons"><svg><use href="#i-video"/></svg><svg><use href="#i-audio"/></svg><svg><use href="#i-cloud"/></svg><svg><use href="#i-book"/></svg></div>
    <p>Sed ut perspiciatis unde omnis iste natus error sit voluptatem accusantium doloremque laudantium, totam rem aperiam</p></div>
  <div class="sermon" style="left:441px;top:3525px"><div class="frame"><div role="img" aria-label="Glowing cross at sunset" style="background:radial-gradient(circle at 50% 50%,#ffe2b0 0%,#d07a40 25%,#4a2a2a 75%,#1a1414 100%)"></div></div>
    <h4>Rebuilding The Walls</h4><div class="meta">Posted on 02 Apr 2013, Pastor: Daniel Hart</div>
    <div class="icons"><svg><use href="#i-video"/></svg><svg><use href="#i-audio"/></svg><svg><use href="#i-cloud"/></svg><svg><use href="#i-book"/></svg></div>
    <p>Sed ut perspiciatis unde omnis iste natus error sit voluptatem accusantium doloremque laudantium, totam rem aperiam</p></div>
  <div class="sermon" style="left:776px;top:3525px"><div class="frame"><div role="img" aria-label="Prayer in a church pew" style="background:linear-gradient(135deg,#4a2e1c,#8a6040 50%,#2a1a10)"></div></div>
    <h4>Rebuilding The Walls</h4><div class="meta">Posted on 02 Apr 2013, Pastor: Daniel Hart</div>
    <div class="icons"><svg><use href="#i-video"/></svg><svg><use href="#i-audio"/></svg><svg><use href="#i-cloud"/></svg><svg><use href="#i-book"/></svg></div>
    <p>Sed ut perspiciatis unde omnis iste natus error sit voluptatem accusantium doloremque laudantium, totam rem aperiam</p></div>
  <div class="sermon" style="left:106px;top:3900px"><div class="frame"><div role="img" aria-label="Hands folded over a rosary" style="background:radial-gradient(circle at 50% 40%,#b08a6a 0%,#4a3428 50%,#141010 100%)"></div></div>
    <h4>Rebuilding The Walls</h4><div class="meta">Posted on 02 Apr 2013, Pastor: Daniel Hart</div>
    <div class="icons"><svg><use href="#i-video"/></svg><svg><use href="#i-audio"/></svg><svg><use href="#i-cloud"/></svg><svg><use href="#i-book"/></svg></div>
    <p>Sed ut perspiciatis unde omnis iste natus error sit voluptatem accusantium doloremque laudantium, totam rem aperiam</p></div>
  <div class="sermon" style="left:441px;top:3900px"><div class="frame"><div role="img" aria-label="Golden cross and chalice" style="background:radial-gradient(circle at 60% 50%,#a0803a 0%,#2a3030 50%,#101818 100%)"></div></div>
    <h4>Rebuilding The Walls</h4><div class="meta">Posted on 02 Apr 2013, Pastor: Daniel Hart</div>
    <div class="icons"><svg><use href="#i-video"/></svg><svg><use href="#i-audio"/></svg><svg><use href="#i-cloud"/></svg><svg><use href="#i-book"/></svg></div>
    <p>Sed ut perspiciatis unde omnis iste natus error sit voluptatem accusantium doloremque laudantium, totam rem aperiam</p></div>
  <div class="sermon" style="left:776px;top:3900px"><div class="frame"><div role="img" aria-label="Hands resting on a Bible" style="background:radial-gradient(circle at 60% 40%,#8a6040 0%,#3a2418 50%,#140c08 100%)"></div></div>
    <h4>Rebuilding The Walls</h4><div class="meta">Posted on 02 Apr 2013, Pastor: Daniel Hart</div>
    <div class="icons"><svg><use href="#i-video"/></svg><svg><use href="#i-audio"/></svg><svg><use href="#i-cloud"/></svg><svg><use href="#i-book"/></svg></div>
    <p>Sed ut perspiciatis unde omnis iste natus error sit voluptatem accusantium doloremque laudantium, totam rem aperiam</p></div>
</section>

<!-- footer -->
<footer class="footer">
  <div class="logo" style="left:106px;top:64px;width:170px">
    <span class="mark" style="width:30px;height:30px;margin-bottom:14px"></span>
    <span style="font-size:26px;letter-spacing:1px">GRACE</span>
    <span style="font-size:12px;letter-spacing:6px">COVENANT</span>
  </div>
  <h5 style="left:358px">Quick Links</h5>
  <div class="flinks">Home<br>About Us<br>Library<br>Donation</div>
  <h5 style="left:551px">Contact Us</h5>
  <div class="contact-row" style="top:116px"><span class="cicon"><svg width="12" height="14"><path d="M6 0a5 5 0 0 1 5 5c0 4-5 9-5 9S1 9 1 5a5 5 0 0 1 5-5z" fill="var(--teal)"/><circle cx="6" cy="5" r="2" fill="var(--dark)"/></svg></span><span>15/A Lorem ipsum dolor sit<br>Westbrook 25kl USA</span></div>
  <div class="contact-row" style="top:180px"><span class="cicon"><svg width="12" height="14"><path d="M2 1h3l1 3-2 1a8 8 0 0 0 4 4l1-2 3 1v3a2 2 0 0 1-2 2C5 13 0 8 0 3a2 2 0 0 1 2-2z" fill="var(--teal)"/></svg></span><span style="line-height:26px">+2 (555) 240 6100</span></div>
  <div class="contact-row" style="top:232px"><span class="cicon"><svg width="14" height="10"><rect width="14" height="10" fill="var(--teal)"/><path d="M0 0l7 5 7-5" stroke="var(--dark)" fill="none"/></svg></span><span style="line-height:26px">info@gracecovenantchurch.com</span></div>
  <h5 style="left:824px">Contact Us</h5>
  <div class="abs" style="left:824px;top:114px;width:270px;height:40px;background:#fff;border-radius:20px;color:#888;font-size:11px;display:flex;align-items:center;padding-left:16px">Enter email</div>
  <span class="btn" style="left:824px;top:164px;width:270px;font-family:'Lato',sans-serif;font-weight:400;font-size:12px">Subscribe</span>
  <div class="abs" style="top:390px;width:1200px;text-align:center;font-size:12px">Copyright © 2023 <span style="color:var(--teal)">Grace Covenant Church</span>. All rights reserved.</div>
  <div class="abs" style="top:392px;left:995px;font-size:9px;color:#555">Updated 14.02.2023 | Layout</div>
</footer>
<div class="social"><span></span><span></span><span></span></div>

</body>
</html>
```